Powepoint Templates From Logo

We need 3 Powerpoint templates for use in a variety of presentations we develop and customize. Primary uses of the powerpoint presentations are for printed "pitch books" describing our firm's capabilities and approach (a lot of words with some design elements that we have developed), printed presentations of the results of financial evaluations of our clients (lots of charts and graphs) and as the talking points for speeches.

The design needs to be professional and "solid" to establish that we are capable of selling your multi-million dollar business, but also be a little different to show that we are not just boring MBA's.

Our current website and other materials have been developed internally and leave a great deal to be desired. I have initiated this project to demonstrate how much our look can be improved and, if successful, I hope to do much bigger projects in the future.
Updates

This is my first project and I thaank you all for your participation. Since I am new to this, I don;t know if I am providing the help and feedback as I should. Please feel free to let me know how I can be a better customer.

Target Market(s)

professionals (lawyers, accountaants), business owners, business groups, technology people

Industry/Entity Type

Financial

Requirements
Must have
• our logo
a place where logo of client can be inserted if appropriate
templates for the following pages
title page
standard bullet narrative page
page for charts and graphs to mostly fill the page
Should not have a lot of dark solid color that has to be printed.

Nice to have
• something to perk up the color a little

```html
<!DOCTYPE html>
<html lang="en">
<head>
<meta charset="utf-8">
<title>Project Title Here</title>
<link href="https://fonts.googleapis.com/css2?family=Arimo:wght@400;700&family=Oswald:wght@700&display=swap" rel="stylesheet">
<style>
  :root {
    --navy: #002b5c;
    --sky-rule: #c7ddf7;
    --mist: #e8f1fb;
    --white: #ffffff;
  }
  * { margin: 0; padding: 0; box-sizing: border-box; }
  html, body {
    width: 1200px;
    height: 900px;
    overflow: hidden;
    background: var(--white);
  }
  .title-slide {
    position: relative;
    width: 1200px;
    height: 900px;
    background: var(--white);
    overflow: hidden;
  }
  .header-wedge {
    position: absolute;
    inset: 0;
    width: 1200px;
    height: 900px;
  }
  .brand {
    position: absolute;
    left: 48px;
    top: 112px;
    display: flex;
    align-items: center;
    gap: 18px;
  }
  .brand-square {
    width: 40px;
    height: 40px;
    background: var(--white);
  }
  .brand-name {
    font-family: "Arimo", Arial, sans-serif;
    font-weight: 700;
    font-size: 50px;
    letter-spacing: 1px;
    color: var(--white);
    line-height: 1;
  }
  .subtitle {
    position: absolute;
    right: 13px;
    top: 386px;
    font-family: "Arimo", Arial, sans-serif;
    font-weight: 700;
    font-size: 40px;
    color: var(--navy);
    line-height: 1;
  }
  .project-title {
    position: absolute;
    left: 54px;
    top: 746px;
    font-family: "Oswald", "Arial Narrow", sans-serif;
    font-weight: 700;
    font-size: 60px;
    color: var(--navy);
    line-height: 1;
    text-transform: uppercase;
  }
  .footer-band {
    position: absolute;
    left: 0;
    bottom: 0;
    width: 1200px;
    height: 23px;
    background: var(--mist);
  }
</style>
</head>
<body>
  <main class="title-slide">
    <svg class="header-wedge" viewBox="0 0 1200 900" aria-hidden="true">
      <polygon points="0,615 1200,255 1200,245 0,605" fill="var(--sky-rule)"/>
      <polygon points="0,0 1200,0 1200,245 0,605" fill="var(--navy)"/>
    </svg>
    <div class="brand">
      <span class="brand-square"></span>
      <span class="brand-name">HARBORLINE</span>
    </div>
    <h2 class="subtitle">Sub title here</h2>
    <h1 class="project-title">Project Title Here</h1>
    <div class="footer-band"></div>
  </main>
</body>
</html>
```